LIFE CHANGING NEW WEBSITE DESIGN NEEDED FOR FULL WEBSITE- FUN/FEMININE!

I need a website designed for a personal financial advice website geared at women called BLUE OTTER LANTERN. I will be providing free financial advice around topics of making, saving, spending and sharing money. The concept is to change the way women understand money and the necessity around building various passive income streams to ensure full financial freedom. This will then carry down to advice for mothers with children and children in particular. The website should be elegant and yet witty. I don't want lots of serious photos but more relatable. I will have a photo of myself and my story as this is a blog and needs to be relatable to women and mothers. I like pinks and greys. I want to have a pink piggy bank being broken with a hammer in the front screen to break our traditional mindset around piggy bank saving/spending habits. I have created a logo that is a pink piggy head with BLUE OTTER LANTERN that needs to be incorporated so that it blends into the heading. I have also already started designing the website on Squarespace and can provide access to that. Basically it should have a format of BLUE OTTER LANTERN LOGO center in header then on left hand navigation: MAKE, SAVE, SPEND, SHARE then on right hand header navigation: MISSION, GET STARTED, CONTACT BOL I would like to have the front page when you go to the url to have the image of the piggy bank being broken then a catchy phrase then under 4 boxes with MAKE (image and description) SAVE (image and description) SPEND (image and description) SHARE (image and description) if you click on those or the title they go to pages that are dedicated to each them. Each page should have a little intro on the topic then I want lots of blog links as I will be mainly writing blogs. Each blog site should have ability to write comments as well. I need social media icons on each page too. Please let me know what you need from me to get started. I prefer having a discussion if possible to not waste anyone's time. I need the site to be easy for me to use and add blogs/urls etc as needed. I also need the site to be put into my domain that I already purchased: www.blueotterlantern-sample.com

Target Market(s)

teenage girls, 20 something girls, 30 something girls and mothers

Coding

Coded - Design and coding required

Number of Pages Required

5+ page

Font styles to use
Sans Serif

Colors
e667a6
e34197
f59195
eea4c8
aaaaaa
cbcbcb
959595

Requirements
Must have
• TOP NAVIGATION
• MAKE SAVE SPEND SHARE LOGO/BLUE OTTER LANTERN MISSION GET STARTED CONTACT BOL
• FRONT PAGE: IMAGE OF PIGGY BANK BEING BROKEN WITH A HAMMER
• CATCH PHRASE OVER THE IMAGE
• BUTTON IN PINK- TAKE ACTION (WHICH DIRECTS TO TAKE ACTION TAB ON NAVIGATION HEADER
• 4 BOXES BELOW MAIN IMAGE WITH IMAGE/DESCRIPTIONS FOR MAKE, SAVE, SPEND, SHARE THAT EACH GO TO THE PAGES FROM THE NAVIGATION HEADER
• EACH PAGE SHOULD BE DEDICATED TO THOSE TOPICS THEN THERE IS AN INTRO ON EACH PAGE THEN THE LINKS TO DIFFERENT BLOGS AROUND EACH TOPIC FOR MAKE, SAVE, SPEND, SHARE
• EACH BLOG SHOULD HAVE COMMENTS SECTION AND SOCIAL MEDIA ICONS
• (GOOD TO USE PINKS/GREYS)
Should not have
• BE SUPER BUSY, CLUTTERED, FEEL LIKE I AM SELLING SOMETHING

```html
<!DOCTYPE html>
<html lang="en">
<head>
<meta charset="utf-8">
<title>Blue Otter Lantern</title>
<link rel="stylesheet" href="https://fonts.googleapis.com/css2?family=Fredoka:wght@500;600;700&family=Roboto:ital,wght@0,400;0,500;0,700;1,400&display=swap">
<style>
:root{
  --pink:#e0278f;
  --pink-box:#e34197;
  --pink-soft:#eea4c8;
  --rose:#f2868f;
  --grey:#7d7d7d;
  --grey-mid:#959595;
  --grey-light:#cbcbcb;
  --ink:#222;
  --text:#555;
  --footer:#2a2a2a;
  --white:#fff;
}
*{box-sizing:border-box;margin:0;padding:0}
html,body{width:1200px;height:3011px;overflow:hidden}
body{position:relative;font-family:"Roboto",Arial,sans-serif;color:var(--text);background:#fff}
.abs{position:absolute}
a{color:inherit;text-decoration:none}

/* top bar */
.topbar{left:0;top:0;width:1200px;height:33px;background:var(--pink);color:#fff;font-size:13px;font-weight:500;display:flex;align-items:center;justify-content:flex-end;padding-right:143px;gap:8px}
.topbar svg{width:12px;height:12px;fill:#fff;vertical-align:-1px;margin-right:5px}

/* header */
.header{left:0;top:33px;width:1200px;height:79px;background:#fff}
.nav{top:33px;height:79px;display:flex;align-items:center;gap:26px;font-size:13px;font-weight:500;color:var(--ink)}
.nav-left{left:143px}
.nav-right{right:143px}
.brand-tab{left:0;top:100px;width:1200px;height:60px;z-index:3}
.brand{left:470px;top:58px;width:260px;text-align:center;z-index:4;font-family:"Fredoka",sans-serif;font-weight:500;font-size:25px;color:var(--pink)}
.brand-dot{display:block;width:38px;height:38px;border:3px solid var(--pink);border-radius:50%;margin:-8px auto 4px}

/* hero */
.hero{left:0;top:112px;width:1200px;height:650px;background:
  radial-gradient(ellipse 330px 300px at 370px 370px,#c9576a 0%,#b34a5c 45%,rgba(150,90,70,0) 75%),
  radial-gradient(ellipse 500px 260px at 200px 600px,#b49a60 0%,rgba(120,100,70,0) 70%),
  linear-gradient(110deg,#6e6257 0%,#7a6a5d 40%,#8a7463 70%,#5f544c 100%)}
.hero-title{left:600px;top:290px;width:500px;text-align:center;font-family:"Fredoka",sans-serif;font-weight:700;font-size:68px;line-height:74px;color:#fff;letter-spacing:1px}
.btn-pink{left:760px;top:479px;width:180px;height:47px;border-radius:24px;background:var(--pink);color:#fff;font-size:16px;font-weight:500;display:flex;align-items:center;justify-content:center;gap:8px}
.btn-pink svg,.btn-outline svg{width:14px;height:14px}
.dots{left:1153px;top:314px;display:flex;flex-direction:column;gap:17px}
.dots span{width:10px;height:10px;border-radius:50%;background:#fff}
.dots span.on{background:transparent;border:2px solid #fff}

/* features */
.features{left:0;top:760px;width:1200px;height:252px;display:flex;z-index:5}
.feature{width:300px;height:252px;text-align:center;color:#fff;position:relative}
.feature.pink{background:var(--pink-box)}
.feature.grey{background:var(--grey)}
.feature-photo{position:absolute;left:66px;top:-86px;width:168px;height:168px;border-radius:50%;border:8px solid}
.feature.pink .feature-photo{border-color:var(--pink-box)}
.feature.grey .feature-photo{border-color:var(--grey)}
.feature h3{position:absolute;top:102px;width:100%;font-size:23px;font-weight:500}
.feature p{position:absolute;top:142px;left:50px;width:200px;font-size:13px;line-height:21px}
.pill{position:absolute;left:92px;top:232px;width:116px;height:38px;border-radius:19px;background:#fff;color:var(--pink);font-size:13px;font-weight:500;display:flex;align-items:center;justify-content:center;box-shadow:0 2px 6px rgba(0,0,0,.15)}
.wedges{left:0;top:700px;width:1200px;height:62px}

/* welcome */
.welcome-bg{left:0;top:1012px;width:1200px;height:668px;background:linear-gradient(180deg,#f6f4f2,#f1efec 60%,#f7f5f3)}
.side-word{font-family:"Roboto",sans-serif;font-weight:700;color:rgba(180,180,180,.22);font-size:82px;letter-spacing:2px;white-space:nowrap;transform:rotate(-90deg);transform-origin:left top}
.mark{width:56px;height:56px;border:4px solid var(--pink-box);border-radius:50%}
.section-title{left:0;width:1200px;text-align:center;font-family:"Fredoka",sans-serif;font-weight:600;font-size:35px;color:var(--ink)}
.welcome-text{left:213px;top:1251px;width:774px;text-align:justify;text-align-last:center;font-size:13.5px;line-height:30.5px}
.welcome-text p+p{margin-top:11px}
.btn-outline{left:491px;top:1480px;width:217px;height:48px;border:2px solid var(--grey-mid);border-radius:24px;color:var(--pink);font-size:16px;font-weight:500;display:flex;align-items:center;justify-content:center;gap:8px}

/* reviews */
.reviews{left:0;top:1600px;width:1200px;height:400px}
.reviews-word{left:0;top:1658px;width:1200px;text-align:center;font-size:82px;font-weight:700;color:rgba(200,80,90,.35);letter-spacing:3px}
.quote{left:570px;top:1684px;font-family:Georgia,serif;font-size:96px;line-height:96px;color:#fff;font-weight:700}
.review-text{left:215px;top:1755px;width:770px;text-align:center;font-size:13.5px;font-style:italic;line-height:28px;color:#fff}
.review-name{left:0;top:1862px;width:1200px;text-align:center;color:#fff;font-size:15px;font-weight:500}
.review-name em{font-size:12px;font-weight:400}
.stars{left:553px;top:1896px;display:flex;gap:3px}
.stars svg{width:15px;height:15px}
.arrow{width:36px;height:36px;border:1.5px solid #fff;border-radius:50%;display:flex;align-items:center;justify-content:center}
.arrow svg{width:12px;height:12px}

/* blog */
.card{top:2212px;width:278px;height:344px;background:#fff;box-shadow:0 2px 10px rgba(0,0,0,.08)}
.card-photo{height:162px}
.date{position:absolute;left:23px;top:178px;width:49px;height:49px;color:#fff;font-size:15px;line-height:19px;text-align:center;padding-top:6px}
.date.pink{background:var(--pink-box)}
.date.grey{background:var(--grey)}
.card h4{position:absolute;left:83px;top:180px;width:165px;font-size:15px;font-weight:500;line-height:22px;color:var(--ink)}
.card p{position:absolute;left:23px;top:240px;width:235px;font-size:12px;line-height:20px;color:#777}
.card a{position:absolute;left:23px;top:310px;font-size:13px;font-weight:500;color:var(--pink)}

/* footer */
.footer-shape{left:0;top:2600px;width:1200px;height:411px}
.footer-brand{left:0;top:2720px;width:1200px;text-align:center;font-family:"Fredoka",sans-serif;font-weight:500;font-size:29px;color:#fff}
.footer-brand .ring{display:block;width:42px;height:42px;border:3px solid #fff;border-radius:50%;margin:0 auto 8px}
.socials{left:500px;top:2837px;width:200px;display:flex;justify-content:space-between}
.socials span{width:34px;height:34px;border:1.5px solid #fff;border-radius:50%}
.footer-nav{left:0;top:2902px;width:1200px;text-align:center;color:#fff;font-size:15.5px;font-weight:500;word-spacing:2px}
.footer-nav i{font-style:normal;margin:0 17px}
.copyright{left:0;top:2945px;width:1200px;text-align:center;color:#fff;font-size:11.5px}
</style>
</head>
<body>

<div class="abs topbar">
  <span><svg viewBox="0 0 24 24"><path d="M6.6 10.8a15.1 15.1 0 0 0 6.6 6.6l2.2-2.2a1 1 0 0 1 1-.25 11.4 11.4 0 0 0 3.6.57 1 1 0 0 1 1 1V20a1 1 0 0 1-1 1A17 17 0 0 1 3 4a1 1 0 0 1 1-1h3.5a1 1 0 0 1 1 1c0 1.25.2 2.45.57 3.57a1 1 0 0 1-.25 1z"/></svg>Call us : 1 555 010 0199</span>
  <span>|</span>
  <span><svg viewBox="0 0 24 24"><path d="M2 5h20v14H2z" fill="none" stroke="#fff" stroke-width="2"/><path d="M2 5l10 8 10-8" fill="none" stroke="#fff" stroke-width="2"/></svg>Email : hello@blueotterlantern-sample.com</span>
</div>

<header class="abs header"></header>
<svg class="abs brand-tab" viewBox="0 0 1200 60" aria-hidden="true"><path d="M465 0H748L730 57H485Z" fill="#fff"/></svg>
<nav class="abs nav nav-left"><a>MAKE</a><a>SAVE</a><a>SPEND</a><a>SHARE</a></nav>
<div class="abs brand"><span class="brand-dot"></span>Blue Otter Lantern</div>
<nav class="abs nav nav-right"><a>MISSION</a><a>GET STARTED</a><a>CONTACT BOL</a></nav>

<section class="abs hero" role="img" aria-label="Photo of a pink piggy bank broken open by a hammer on a wooden table, coins and notes spilling out"></section>
<h1 class="abs hero-title">BLUE OTTER LANTERN</h1>
<a class="abs btn-pink">TAKE ACTION <svg viewBox="0 0 16 16"><circle cx="8" cy="8" r="8" fill="#fff"/><path d="M5 8h5M8 5l3 3-3 3" stroke="#e0278f" stroke-width="2" fill="none"/></svg></a>
<div class="abs dots"><span></span><span></span><span class="on"></span><span></span><span></span></div>

<svg class="abs wedges" viewBox="0 0 1200 62" aria-hidden="true">
  <path d="M0 12L70 62H0Z" fill="#e34197"/>
  <path d="M1200 12L1120 62H1200Z" fill="#e34197"/>
</svg>

<!-- welcome background (placed beneath the feature boxes) -->
<section class="abs welcome-bg" role="img" aria-label="Faded background photo of scattered coins"></section>

<section class="abs features">
  <div class="feature pink">
    <div class="feature-photo" role="img" aria-label="Hand holding glowing dollar symbols" style="background:radial-gradient(circle at 55% 45%,#4f8fc0,#1c3a63 70%)"></div>
    <h3>MAKE</h3>
    <p>At vero eos et accusamus et iusto odio dignissimos ducimus qui blanditiis praesentium</p>
    <a class="pill">READ MORE</a>
  </div>
  <div class="feature grey">
    <div class="feature-photo" role="img" aria-label="Coin dropped into a pink piggy bank" style="background:radial-gradient(circle at 50% 60%,#e8687e,#c9a9a4 70%)"></div>
    <h3>SAVE</h3>
    <p>At vero eos et accusamus et iusto odio dignissimos ducimus qui blanditiis praesentium</p>
    <a class="pill">READ MORE</a>
  </div>
  <div class="feature pink">
    <div class="feature-photo" role="img" aria-label="Hands paying online with a card on a laptop" style="background:radial-gradient(circle at 50% 55%,#9a8c82,#e6e2de 75%)"></div>
    <h3>SPEND</h3>
    <p>At vero eos et accusamus et iusto odio dignissimos ducimus qui blanditiis praesentium</p>
    <a class="pill">READ MORE</a>
  </div>
  <div class="feature grey">
    <div class="feature-photo" role="img" aria-label="Businessman facing a glowing network of connections" style="background:radial-gradient(circle at 50% 50%,#3fa3c4,#0f3d57 75%)"></div>
    <h3>SHARE</h3>
    <p>At vero eos et accusamus et iusto odio dignissimos ducimus qui blanditiis praesentium</p>
    <a class="pill">READ MORE</a>
  </div>
</section>

<!-- welcome -->
<div class="abs side-word" style="left:52px;top:1575px">WELCOME</div>
<svg class="abs" style="left:1040px;top:1175px" width="160" height="310" viewBox="0 0 160 310" aria-hidden="true">
  <circle cx="160" cy="155" r="150" fill="none" stroke="#f4c6dd" stroke-width="10"/>
  <circle cx="160" cy="155" r="90" fill="none" stroke="#f2b4d2" stroke-width="10"/>
</svg>
<div class="abs mark" style="left:572px;top:1100px"></div>
<h2 class="abs section-title" style="top:1180px">Welcome to Blue Otter Lantern (BOL)!</h2>
<div class="abs welcome-text">
  <p>My mission is simple- I want to challenge you to rethink the way you think about growing, spending and saving money. By redesigning your life around your finances I want you to run your life as if you are the CEO of your own business, and the business is maximising the value and profitability of your life.</p>
  <p>It is shocking that in today's world of information we are we still live in a society where most educated people leave school without even a basic understanding of money and how to run their lives outside of a just obtaining a job. Instead, we are taught to work hard in school, find a good job, get married, have children, save up for big expenses (like homes, school tuition..)</p>
</div>
<a class="abs btn-outline">READ MORE INFO <svg viewBox="0 0 16 16"><circle cx="8" cy="8" r="8" fill="#e0278f"/><path d="M5 8h5M8 5l3 3-3 3" stroke="#fff" stroke-width="2" fill="none"/></svg></a>

<!-- reviews -->
<svg class="abs reviews" viewBox="0 0 1200 400" aria-hidden="true">
  <path d="M0 79H1200V319H0Z" fill="#f2868f"/>
  <path d="M215 79Q600 -40 985 79Z" fill="#f2868f"/>
  <path d="M215 319Q600 440 985 319Z" fill="#f2868f"/>
  <path d="M220 76Q600 -50 980 76" fill="none" stroke="#7d7d7d" stroke-width="4"/>
  <path d="M220 324Q600 450 980 324" fill="none" stroke="#7d7d7d" stroke-width="4"/>
</svg>
<div class="abs reviews-word">REVIEWS</div>
<div class="abs quote">&#8220;</div>
<p class="abs review-text">At vero eos et accusamus et iusto odio dignissimos ducimus qui blanditiis praesentium voluptatum deleniti atque corrupti quos dolores et quas molestias excepturi sint occaecati cupiditate non provident, similique sunt in culpa qui officia deserunt mollitia animi, id est laborum et dolorum fugam quidem rerum facilis est et expoluta nobis est eligendi optio cumque nihil impedit quo minus</p>
<div class="abs review-name">- MARA QUILL, <em>Customer</em></div>
<div class="abs stars">
  <svg viewBox="0 0 24 24"><path d="M12 2l3 7h7l-5.5 4.5 2 7.5L12 17l-6.5 4 2-7.5L2 9h7z" fill="none" stroke="#fff" stroke-width="1.6"/></svg>
  <svg viewBox="0 0 24 24"><path d="M12 2l3 7h7l-5.5 4.5 2 7.5L12 17l-6.5 4 2-7.5L2 9h7z" fill="none" stroke="#fff" stroke-width="1.6"/></svg>
  <svg viewBox="0 0 24 24"><path d="M12 2l3 7h7l-5.5 4.5 2 7.5L12 17l-6.5 4 2-7.5L2 9h7z" fill="none" stroke="#fff" stroke-width="1.6"/></svg>
  <svg viewBox="0 0 24 24"><path d="M12 2l3 7h7l-5.5 4.5 2 7.5L12 17l-6.5 4 2-7.5L2 9h7z" fill="none" stroke="#fff" stroke-width="1.6"/></svg>
  <svg viewBox="0 0 24 24"><path d="M12 2l3 7h7l-5.5 4.5 2 7.5L12 17l-6.5 4 2-7.5L2 9h7z" fill="none" stroke="#fff" stroke-width="1.6"/></svg>
</div>
<a class="abs arrow" style="left:130px;top:1782px"><svg viewBox="0 0 12 12"><path d="M8 1L3 6l5 5" stroke="#fff" stroke-width="1.6" fill="none"/></svg></a>
<a class="abs arrow" style="left:1034px;top:1782px"><svg viewBox="0 0 12 12"><path d="M4 1l5 5-5 5" stroke="#fff" stroke-width="1.6" fill="none"/></svg></a>

<!-- blog -->
<svg class="abs" style="left:0;top:1915px" width="170" height="310" viewBox="0 0 170 310" aria-hidden="true">
  <circle cx="10" cy="155" r="150" fill="none" stroke="#f4c6dd" stroke-width="10"/>
  <circle cx="10" cy="155" r="70" fill="none" stroke="#f2b4d2" stroke-width="10"/>
</svg>
<div class="abs side-word" style="left:1092px;top:2478px">BLOG POSTS</div>
<div class="abs mark" style="left:572px;top:2064px"></div>
<h2 class="abs section-title" style="top:2132px">Blog Posts</h2>

<article class="abs card" style="left:145px">
  <div class="card-photo" role="img" aria-label="Woman on the phone at a bright office desk" style="background:linear-gradient(135deg,#eef0f2,#d9dde0)"></div>
  <div class="date pink">12<br>JAN</div>
  <h4>Pellentesque faucibus Ut accumsan ultric</h4>
  <p>Duis quam Nam eget lacus Aliquam erat volutpat Quisque dignissim congue leo Mauris vel la vestibulum</p>
  <a>READ MORE</a>
</article>
<article class="abs card" style="left:462px">
  <div class="card-photo" role="img" aria-label="Two women talking over a laptop" style="background:linear-gradient(135deg,#8a6a55,#c9b7a6)"></div>
  <div class="date grey">12<br>JAN</div>
  <h4>Pellentesque faucibus Ut accumsan ultric</h4>
  <p>Duis quam Nam eget lacus Aliquam erat volutpat Quisque dignissim congue leo Mauris vel la vestibulum</p>
  <a>READ MORE</a>
</article>
<article class="abs card" style="left:778px">
  <div class="card-photo" role="img" aria-label="Hands reviewing financial charts with a calculator" style="background:linear-gradient(135deg,#b9c3d6,#eef1f6)"></div>
  <div class="date pink">12<br>JAN</div>
  <h4>Pellentesque faucibus Ut accumsan ultric</h4>
  <p>Duis quam Nam eget lacus Aliquam erat volutpat Quisque dignissim congue leo Mauris vel la vestibulum</p>
  <a>READ MORE</a>
</article>

<!-- footer -->
<svg class="abs footer-shape" viewBox="0 0 1200 411" aria-hidden="true">
  <circle cx="1200" cy="210" r="150" fill="none" stroke="#f4c6dd" stroke-width="10"/>
  <path d="M0 130Q600 20 1200 130V411H0Z" fill="#959595"/>
  <path d="M0 160Q600 40 1200 160V411H0Z" fill="#e34197"/>
  <path d="M0 215Q230 80 600 68Q970 80 1200 215V411H0Z" fill="#2a2a2a"/>
</svg>
<div class="abs footer-brand"><span class="ring"></span>Blue Otter Lantern</div>
<div class="abs socials" aria-label="Social media links"><span></span><span></span><span></span><span></span><span></span></div>
<nav class="abs footer-nav">MAKE<i>/</i>SAVE<i>/</i>SPEND<i>/</i>SHARE<i>/</i>MISSION<i>/</i>GET STARTED<i>/</i>CONTACT BOL</nav>
<div class="abs copyright">©2019 BLUE OTTER LANTERN. All Rights Reserved &nbsp;|&nbsp; Privacy Policy</div>

</body>
</html>
```